Tellmora Corporate Stationery

Look for design of all new corporate stationery for an existing insurance broking business that is going through a redesign and move from older partners to younger family members. New Logo is attached. Company is Brisbane based.
Colours in the Logo is Hex #43bed8 and website features a lot of hex #17b8d8. Website front page "A plan to protect you" - headline. "Professional and Individual advice to protect your greatest assets" - tagline.

Stationery required: Business Cards, Letter head, Thank-you cards, Birthday cards, Presentation folders, With Compliment slips and a powerpoint template. We also would like to send a card to all customers with the something along of the lines of "something new".

Target Market(s)

Customers of Insurance business looking at superannuation, life and income protection insurance, investment advice and wills

Industry/Entity Type

Insurance Broker

Font styles to use
Other font styles liked:
• same as logo

Requirements
Must have
• The above designs for new stationery for the new business including:
• Business Cards, Letter head, Thank-you cards, Birthday cards, Presentation folders, With Compliment slips and a powerpoint template. We also would like to send a card to all customers with the something along of the lines of "something new".
Nice to have
• It is a new look - long time family business being passed to next generation - big focus on advice for YOU, individual advice etc..

```html
<!DOCTYPE html>
<html lang="en">
<head>
<meta charset="utf-8">
<title>Tellmora Business Card</title>
<link rel="stylesheet" href="https://fonts.googleapis.com/css2?family=Source+Sans+3:wght@400;600&display=swap">
<style>
  :root {
    --backdrop: #d8d5d1;
    --card-light: #eceeef;
    --panel-dark: #3b3c3e;
    --stripe-dark: #2e2f31;
    --teal: #2fa3b6;
    --teal-bright: #3ab7cb;
    --text-light: #d4d5d7;
    --text-soft: #b7b8ba;
  }
  * { margin: 0; padding: 0; box-sizing: border-box; }
  html, body { width: 1200px; height: 969px; overflow: hidden; background: var(--backdrop); }
  body { font-family: "Source Sans 3", "Helvetica Neue", Arial, sans-serif; }

  .business-card {
    position: absolute; left: 100px; top: 200px;
    width: 1000px; height: 568px;
    background: var(--card-light);
    box-shadow: 0 12px 40px rgba(0,0,0,0.18);
    overflow: hidden;
  }
  .card-shapes { position: absolute; inset: 0; width: 100%; height: 100%; }

  .brand {
    position: absolute; left: 150px; top: 282px;
    display: flex; align-items: center; gap: 16px;
  }
  .brand-dot { width: 34px; height: 34px; border-radius: 50%; background: var(--teal); }
  .brand-name {
    font-size: 56px; font-weight: 600; letter-spacing: 1px;
    color: var(--teal); line-height: 1;
  }

  .contact-block {
    position: absolute; right: 54px; top: 118px;
    text-align: right; color: var(--text-light);
  }
  .person-name { font-size: 30px; font-weight: 400; color: var(--teal-bright); letter-spacing: 1px; line-height: 1.2; }
  .person-role { font-size: 23px; letter-spacing: 0.5px; line-height: 1.3; margin-bottom: 18px; }
  .address-line { font-size: 23px; line-height: 1.55; }
  .contact-list { list-style: none; margin-top: 22px; }
  .contact-item {
    display: flex; justify-content: flex-end; align-items: center; gap: 14px;
    font-size: 23px; line-height: 38px;
  }
  .contact-item.is-muted { color: var(--text-soft); }
  .contact-icon { width: 22px; height: 22px; fill: var(--teal-bright); flex: none; }
</style>
</head>
<body>
  <div class="business-card">
    <svg class="card-shapes" viewBox="0 0 1000 568" preserveAspectRatio="none" aria-hidden="true">
      <polygon points="611,0 632,0 456,568 422,568" fill="var(--stripe-dark)"/>
      <polygon points="628,0 648,0 474,568 453,568" fill="var(--teal)"/>
      <polygon points="650,0 1000,0 1000,568 477,568" fill="var(--panel-dark)"/>
    </svg>

    <div class="brand">
      <span class="brand-dot"></span>
      <span class="brand-name">TELLMORA</span>
    </div>

    <div class="contact-block">
      <p class="person-name">DANIEL HART</p>
      <p class="person-role">CEO/FOUNDER</p>
      <p class="address-line">214 Wattle Grove Road</p>
      <p class="address-line">Brisbane, Queensland 4000</p>
      <ul class="contact-list">
        <li class="contact-item">731 482 5906
          <svg class="contact-icon" viewBox="0 0 24 24"><path d="M6.6 10.8a15.1 15.1 0 0 0 6.6 6.6l2.2-2.2c.3-.3.7-.4 1-.2 1.1.4 2.3.6 3.6.6.6 0 1 .4 1 1V20c0 .6-.4 1-1 1A17 17 0 0 1 3 4c0-.6.4-1 1-1h3.5c.6 0 1 .4 1 1 0 1.3.2 2.5.6 3.6.1.3 0 .7-.2 1z"/></svg>
        </li>
        <li class="contact-item">417 259 8830
          <svg class="contact-icon" viewBox="0 0 24 24"><path d="M7 1h10a2 2 0 0 1 2 2v18a2 2 0 0 1-2 2H7a2 2 0 0 1-2-2V3a2 2 0 0 1 2-2zm0 3v15h10V4z"/></svg>
        </li>
        <li class="contact-item">731 482 5917
          <svg class="contact-icon" viewBox="0 0 24 24"><path d="M6 3h12v5H6zM4 9h16a2 2 0 0 1 2 2v6h-4v4H6v-4H2v-6a2 2 0 0 1 2-2zm4 6v4h8v-4z"/></svg>
        </li>
        <li class="contact-item is-muted">hello@tellmora.com
          <svg class="contact-icon" viewBox="0 0 24 24"><path d="M2 5h20v14H2zm2 2v.5l8 5 8-5V7l-8 5z"/></svg>
        </li>
        <li class="contact-item is-muted">www.tellmora.com
          <svg class="contact-icon" viewBox="0 0 24 24"><path d="M12 2a10 10 0 1 0 0 20 10 10 0 0 0 0-20zm-1 17.9A8 8 0 0 1 4.1 11H7c.1 3.3 1.4 6.3 4 8.9zm0-10.9H7.1c.4-2.6 1.6-5 3.9-6.9zm2 0V4.2c2 1.7 3.2 3 3.8 4.8zm0 2h4c-.2 3.2-1.6 6.1-4 8.4zm2.6 8.2A11.9 11.9 0 0 0 17 11h2.9a8 8 0 0 1-4.3 7.2z"/></svg>
        </li>
      </ul>
    </div>
  </div>
</body>
</html>
```